web page design with coding

We are a start up insurance agency who needs to design a full functional web page. we recently did a postcard design though drawkettle I will upload the final project for you to see the color scheme/font we would like to continue to use. I also have a rough draft of verbage I would like our website to have. I will upload that as well.

Reason: I am sorry but the person who will make the final decision on the website is out of the country at the moment and will make the final decision when he returns.

Industry/Entity Type

Insurance

Coding

Coded - Design and coding required

```html
<!DOCTYPE html>
<html lang="en">
<head>
<meta charset="utf-8">
<title>Corvella Insurance Group</title>
<link rel="stylesheet" href="https://fonts.googleapis.com/css2?family=Cinzel:wght@400;700&family=Open+Sans:ital,wght@0,400;0,600;0,700;1,400&display=swap">
<style>
:root{
  --navy:#16407a;
  --navy-deep:#0f2f5e;
  --green:#2f7d3f;
  --green-light:#3a9a4c;
  --ink:#1d1d1d;
  --body:#6a6a6a;
  --rule:#dcdcdc;
  --panel:#eef0f3;
  --white:#ffffff;
  --footer:#1f1c19;
}
*{box-sizing:border-box;margin:0;padding:0}
html,body{width:1200px;height:2305px;overflow:hidden;background:var(--white)}
body{position:relative;font-family:"Open Sans",Arial,sans-serif;color:var(--body)}
.abs{position:absolute}

/* hero */
.hero{position:absolute;left:0;top:0;width:1200px;height:575px;overflow:hidden}
.hero-photo{position:absolute;inset:0;background:linear-gradient(180deg,#b9d3ec 0%,#d9e6f1 30%,#e8e4dc 50%,#c9c4b8 62%,#6f9a52 78%,#4d7b3a 100%)}
.top-strip{position:absolute;left:0;top:0;width:1200px;height:4px;background:var(--navy)}
.brand{position:absolute;left:101px;top:38px;display:flex;align-items:center;gap:10px}
.brand-square{width:14px;height:14px;background:var(--navy);flex:none}
.brand-name{font-family:"Open Sans",Arial,sans-serif;font-size:14px;font-weight:700;line-height:17px;color:var(--navy)}
.nav{position:absolute;left:311px;top:40px;display:flex;gap:28px;font-size:14px;font-weight:700;color:#1c1c1c}
.nav .active{color:var(--green)}
.search{position:absolute;left:857px;top:43px}
.call{position:absolute;left:893px;top:26px;display:flex;gap:14px}
.call-ico{width:32px;height:32px;border-radius:50%;background:var(--green);display:flex;align-items:center;justify-content:center}
.call-label{font-size:14px;color:#333}
.call-num{font-size:23px;font-weight:700;color:var(--navy);line-height:1.1}
.hero-title{position:absolute;left:0;width:1200px;top:222px;text-align:center;font-family:"Cinzel",Georgia,serif;font-size:46px;font-weight:400;color:#1a1a1a}
.hero-sub{position:absolute;left:0;width:1200px;top:278px;text-align:center;font-size:28px;color:var(--navy)}
.btn-quote{position:absolute;left:509px;top:333px;width:182px;height:40px;background:var(--green);color:#fff;font-weight:700;font-size:16px;display:flex;align-items:center;justify-content:center;border:2px solid #fff}
.dots{position:absolute;left:533px;top:499px;display:flex;gap:5px}
.dots span{width:30px;height:6px;background:#fff;border-radius:3px}
.dots span:first-child{background:var(--green)}
.hero-wave{position:absolute;left:0;top:430px}

/* welcome */
.h2{font-family:"Cinzel",Georgia,serif;font-size:25px;font-weight:400;color:#111}
.welcome-title{left:98px;top:608px}
.welcome-photo{left:98px;top:670px;width:208px;height:246px;border:4px solid #fff;box-shadow:0 0 0 1px var(--rule);background:linear-gradient(160deg,#9aa3ab 0%,#5f666d 55%,#c9c9c9 100%)}
.copy{font-size:12.5px;line-height:22.5px;color:var(--body)}
.welcome-copy{left:327px;top:662px;width:445px}
.welcome-copy p{margin-bottom:22px}
.more{left:326px;top:898px;font-size:13px;font-weight:700;color:var(--green)}
.quote-box{left:788px;top:616px;width:314px;height:301px;background:#f5f6f7;border:1px solid #e2e2e2}
.quote-head{height:42px;background:var(--navy);color:#fff;font-family:"Cinzel",Georgia,serif;font-size:21px;display:flex;align-items:center;justify-content:center}
.field{position:absolute;left:14px;width:284px;height:38px;background:#fff;border:1px solid #dedede;font-size:12px;color:#666;padding:11px 13px}
.select-arrow{position:absolute;right:0;top:0;width:36px;height:36px;background:#e9e9e9;display:flex;align-items:center;justify-content:center}
.send{position:absolute;left:14px;top:247px;width:284px;height:40px;background:var(--green);color:#fff;font-weight:700;font-size:16px;display:flex;align-items:center;justify-content:center}

/* lines */
.lines{left:0;top:968px;width:1200px;height:569px;background:var(--panel)}
.lines-title{left:100px;top:1004px}
.lines-photo{left:98px;top:1063px;width:235px;height:139px;border:4px solid #fff;box-shadow:0 0 0 1px var(--rule);background:linear-gradient(180deg,#c7d8e6 0%,#d7c7b0 45%,#7ea05a 100%)}
.lines-copy{left:364px;top:1056px;width:720px}
.lines-copy p{margin-bottom:21px}
.col-label{font-size:13px;font-weight:700;color:#111}
.list{list-style:none;font-size:12px;color:#555}
.list li{height:27.5px;display:flex;align-items:center;gap:10px}
.list svg{flex:none}

/* testimonials */
.t-title{left:0;width:1200px;top:1570px;text-align:center}
.t-ring{left:107px;top:1620px;width:110px;height:110px;border-radius:50%;background:#e8e8e8;display:flex;align-items:center;padding-left:22px;font-family:Georgia,serif;font-size:80px;color:#cfcfcf}
.t-portrait{left:176px;top:1617px;width:110px;height:110px;border-radius:50%;background:linear-gradient(180deg,#dfe3e8 0%,#b9bfc6 100%)}
.t-quote{left:320px;top:1624px;width:775px;font-style:italic;font-size:13px;line-height:23px;color:#666}
.t-name{left:320px;top:1707px;font-family:"Cinzel",Georgia,serif;font-size:15px;font-weight:700;color:var(--navy)}

/* footer */
.footer-photo{left:0;top:1790px;width:1200px;height:515px;background:linear-gradient(180deg,#3a3430 0%,#26221e 45%,#1b1916 100%)}
.footer-wave{left:0;top:1775px}
.f-title{left:0;width:1200px;top:1846px;text-align:center;font-family:"Cinzel",Georgia,serif;font-size:27px;color:#fff}
.f-label{font-size:15px;font-weight:700;color:#fff}
.f-small{font-size:11px;color:#fff}
.input{position:absolute;background:#fff}
.submit{left:642px;top:2174px;width:86px;height:39px;border:2px solid #fff;color:#fff;font-size:12px;font-weight:700;display:flex;align-items:center;justify-content:center}
.info-row{left:808px;display:flex;align-items:center;gap:14px;color:#fff;font-size:15px}
.ring{width:36px;height:36px;border:2px solid #fff;border-radius:50%;display:flex;align-items:center;justify-content:center;flex:none}
.socials{left:810px;top:2180px;display:flex;gap:14px}
.socials span{width:26px;height:26px;background:#fff;border-radius:4px}
.f-rule{left:98px;top:2240px;width:1004px;height:1px;background:#5a5550}
.copyright{left:0;width:1200px;top:2265px;text-align:center;font-size:11px;color:#ddd}
</style>
</head>
<body>

<header class="hero">
  <div class="hero-photo" role="img" aria-label="Photo of a two-storey family house with a front lawn and a parked car"></div>
  <div class="top-strip"></div>
  <div class="brand"><span class="brand-square"></span><span class="brand-name">Corvella<br>Insurance Group</span></div>
  <nav class="nav"><span class="active">HOME</span><span>ABOUT US</span><span>PRODUCTS &amp; SERVICES</span><span>AGENTS</span><span>CONTACT US</span></nav>
  <svg class="search" width="14" height="14" viewBox="0 0 14 14"><circle cx="5.5" cy="5.5" r="4" fill="none" stroke="#1c1c1c" stroke-width="2"/><line x1="8.5" y1="8.5" x2="13" y2="13" stroke="#1c1c1c" stroke-width="2.4"/></svg>
  <div class="call">
    <div class="call-ico"><svg width="16" height="16" viewBox="0 0 24 24"><path fill="#fff" d="M6.6 10.8a15.1 15.1 0 0 0 6.6 6.6l2.2-2.2c.3-.3.7-.4 1-.2 1.1.4 2.3.6 3.6.6.6 0 1 .4 1 1V20c0 .6-.4 1-1 1A17 17 0 0 1 3 4c0-.6.4-1 1-1h3.5c.6 0 1 .4 1 1 0 1.3.2 2.5.6 3.6.1.3 0 .7-.2 1z"/></svg></div>
    <div><div class="call-label">Call Us Today</div><div class="call-num">(305) 555-0147</div></div>
  </div>
  <h1 class="hero-title">Corvella Insurance Group</h1>
  <p class="hero-sub">We are a start up insurance agency</p>
  <div class="btn-quote">GET A QUOTE</div>
  <div class="dots"><span></span><span></span><span></span><span></span></div>
  <svg class="hero-wave" width="1200" height="145" viewBox="0 0 1200 145">
    <path d="M0 40 C250 120 650 130 1200 45 L1200 145 L0 145 Z" fill="var(--green)"/>
    <path d="M0 40 C250 120 600 130 880 95 C700 135 300 130 0 100 Z" fill="var(--navy)"/>
    <path d="M0 70 C300 135 700 140 1200 62 L1200 145 L0 145 Z" fill="#fff"/>
  </svg>
</header>

<section class="welcome">
  <h2 class="h2 abs welcome-title">Welcome to Corvella Insurance Group</h2>
  <div class="abs welcome-photo" role="img" aria-label="Photo of a businessman drawing a red roof over icons of a house, a family and a car"></div>
  <div class="abs copy welcome-copy">
    <p>Corvella Insurance Group has joined with regional &amp; national insurance companies to provide quality products and superior service. We take the time to discuss options and coverages, not to just sell insurance products. We strive to educate you in the decision making process to become an informed consumer.</p>
    <p>We specialize in commercial business &amp; personal insurance. We are committed to providing personal attention to all your insurance needs.</p>
    <p>At Corvella Insurance Group, we are independent insurance agents.</p>
  </div>
  <div class="abs more">READ MORE &gt;&gt;</div>

  <form class="abs quote-box">
    <div class="quote-head">Insurance Quote</div>
    <div class="field" style="top:56px">Name * :</div>
    <div class="field" style="top:104px">Email * :</div>
    <div class="field" style="top:152px">Phone * :</div>
    <div class="field" style="top:196px">Select Insurance type :
      <span class="select-arrow"><svg width="10" height="6"><path d="M0 0h10L5 6z" fill="#888"/></svg></span></div>
    <div class="send">SEND</div>
  </form>
</section>

<section class="abs lines"></section>
<h2 class="h2 abs lines-title">Business &amp; Personal Insurance</h2>
<div class="abs lines-photo" role="img" aria-label="Photo of a smiling couple on a lawn in front of their house"></div>
<div class="abs copy lines-copy">
  <p>Corvella Insurance Group is a one stop shop for all of your personal and business insurance needs. With our established relationships and market knowledge, we will tailor an insurance program specifically designed to meet your needs.</p>
  <p>As an independent insurance agency, we are able to provide you with a wide variety of plans and carriers. Corvella Insurance Group represents top insurance carriers in the marketplace.</p>
  <p>Click a link below to learn more about the different types of insurance we offer.</p>
</div>

<div class="abs col-label" style="left:98px;top:1234px">BUSINESS INSURANCE :</div>
<div class="abs col-label" style="left:746px;top:1234px">PERSONAL INSURANCE :</div>

<svg width="0" height="0" style="position:absolute"><defs><symbol id="arrow" viewBox="0 0 12 12"><path d="M0 4.5h6.5V1L12 6l-5.5 5V7.5H0z" fill="var(--green)"/></symbol></defs></svg>

<ul class="abs list" style="left:98px;top:1269px">
  <li><svg width="12" height="12"><use href="#arrow"/></svg>Bond</li>
  <li><svg width="12" height="12"><use href="#arrow"/></svg>Builders Risk</li>
  <li><svg width="12" height="12"><use href="#arrow"/></svg>Business Owners Policy (BOP)</li>
  <li><svg width="12" height="12"><use href="#arrow"/></svg>Commercial Auto</li>
  <li><svg width="12" height="12"><use href="#arrow"/></svg>Crime</li>
  <li><svg width="12" height="12"><use href="#arrow"/></svg>Crop / Hail</li>
  <li><svg width="12" height="12"><use href="#arrow"/></svg>Difference in Conditions</li>
  <li><svg width="12" height="12"><use href="#arrow"/></svg>Directors and Officers (D&amp;O)</li>
</ul>
<ul class="abs list" style="left:315px;top:1269px">
  <li><svg width="12" height="12"><use href="#arrow"/></svg>Employment Practices Liability</li>
  <li><svg width="12" height="12"><use href="#arrow"/></svg>Errors &amp; Omissions (E&amp;O)</li>
  <li><svg width="12" height="12"><use href="#arrow"/></svg>Equipment Breakdown</li>
  <li><svg width="12" height="12"><use href="#arrow"/></svg>Garage</li>
  <li><svg width="12" height="12"><use href="#arrow"/></svg>General Liability</li>
  <li><svg width="12" height="12"><use href="#arrow"/></svg>Inland Marine</li>
  <li><svg width="12" height="12"><use href="#arrow"/></svg>Liquor Liability</li>
  <li><svg width="12" height="12"><use href="#arrow"/></svg>Medical Malpractice</li>
</ul>
<ul class="abs list" style="left:530px;top:1269px">
  <li><svg width="12" height="12"><use href="#arrow"/></svg>OCP</li>
  <li><svg width="12" height="12"><use href="#arrow"/></svg>Professional Liability</li>
  <li><svg width="12" height="12"><use href="#arrow"/></svg>Property</li>
  <li><svg width="12" height="12"><use href="#arrow"/></svg>Truckers</li>
  <li><svg width="12" height="12"><use href="#arrow"/></svg>Umbrella</li>
  <li><svg width="12" height="12"><use href="#arrow"/></svg>Workers Compensation</li>
</ul>
<ul class="abs list" style="left:747px;top:1269px">
  <li><svg width="12" height="12"><use href="#arrow"/></svg>Auto</li>
  <li><svg width="12" height="12"><use href="#arrow"/></svg>Boat &amp; Marine</li>
  <li><svg width="12" height="12"><use href="#arrow"/></svg>Collector Car</li>
  <li><svg width="12" height="12"><use href="#arrow"/></svg>Condo</li>
  <li><svg width="12" height="12"><use href="#arrow"/></svg>Flood</li>
  <li><svg width="12" height="12"><use href="#arrow"/></svg>High Net Worth</li>
  <li><svg width="12" height="12"><use href="#arrow"/></svg>Homeowners</li>
  <li><svg width="12" height="12"><use href="#arrow"/></svg>Rental and Investment Property</li>
</ul>
<ul class="abs list" style="left:963px;top:1269px">
  <li><svg width="12" height="12"><use href="#arrow"/></svg>Mobile Home</li>
  <li><svg width="12" height="12"><use href="#arrow"/></svg>Motor Home</li>
  <li><svg width="12" height="12"><use href="#arrow"/></svg>Motorcycle</li>
  <li><svg width="12" height="12"><use href="#arrow"/></svg>Personal Umbrella</li>
  <li><svg width="12" height="12"><use href="#arrow"/></svg>Recreational Vehicles</li>
  <li><svg width="12" height="12"><use href="#arrow"/></svg>Renters</li>
  <li><svg width="12" height="12"><use href="#arrow"/></svg>Travel</li>
  <li><svg width="12" height="12"><use href="#arrow"/></svg>Valuable Items</li>
</ul>

<section class="testimonials">
  <h2 class="h2 abs t-title">Client Testimonials</h2>
  <svg class="abs" style="left:84px;top:1664px" width="12" height="20"><path d="M10 1 2 10l8 9" fill="none" stroke="#bbb" stroke-width="2"/></svg>
  <svg class="abs" style="left:1104px;top:1664px" width="12" height="20"><path d="M2 1l8 9-8 9" fill="none" stroke="#bbb" stroke-width="2"/></svg>
  <div class="abs t-ring">&ldquo;</div>
  <div class="abs t-portrait" role="img" aria-label="Portrait photo of the client in a suit"></div>
  <p class="abs t-quote">It is a long established fact that a reader will be distracted by the readable content of a page when looking at its layout. The point of using Lorem Ipsum is that it has a more-or-less normal distribution of letters, as opposed to using 'Content here, content here', making it look like readable English.</p>
  <div class="abs t-name">- Mara Ellison</div>
</section>

<footer>
  <div class="abs footer-photo" role="img" aria-label="Dimmed photo of a family outdoors"></div>
  <svg class="abs footer-wave" width="1200" height="110" viewBox="0 0 1200 110">
    <path d="M0 0H1200V40C900 0 400 -10 0 75Z" fill="#fff"/>
    <path d="M0 75C400 -10 900 0 1200 40 L1200 60 C900 20 400 15 0 100Z" fill="var(--navy)"/>
    <path d="M600 15C850 10 1050 20 1200 40 L1200 65 C1050 40 850 28 600 15Z" fill="var(--green)"/>
  </svg>
  <h2 class="abs f-title">Contact Us</h2>

  <div class="abs f-label" style="left:98px;top:1901px">CONTACT FORM</div>
  <div class="abs f-small" style="left:100px;top:1941px">NAME :</div>
  <div class="abs f-small" style="left:418px;top:1941px">PHONE :</div>
  <div class="input" style="left:100px;top:1959px;width:310px;height:34px"></div>
  <div class="input" style="left:418px;top:1959px;width:310px;height:34px"></div>
  <div class="abs f-small" style="left:100px;top:2003px">EMAIL :</div>
  <div class="input" style="left:100px;top:2022px;width:628px;height:32px"></div>
  <div class="abs f-small" style="left:100px;top:2064px">MESSAGE :</div>
  <div class="input" style="left:100px;top:2080px;width:628px;height:83px"></div>
  <div class="abs submit">SUBMIT</div>

  <div class="abs f-label" style="left:810px;top:1901px">CONTACT INFORMATION</div>
  <div class="abs info-row" style="top:1961px">
    <span class="ring"><svg width="14" height="18" viewBox="0 0 14 18"><path d="M7 1a6 6 0 0 0-6 6c0 4.5 6 10 6 10s6-5.5 6-10a6 6 0 0 0-6-6z" fill="none" stroke="#fff" stroke-width="1.8"/><circle cx="7" cy="7" r="2" fill="#fff"/></svg></span>
    <span style="font-size:14px;line-height:23px">1820 Harbor Lane, Suite 300<br>Coral Bay, FL 33000</span>
  </div>
  <div class="abs info-row" style="top:2019px">
    <span class="ring"><svg width="16" height="12" viewBox="0 0 16 12"><rect width="16" height="12" rx="1.5" fill="#fff"/><path d="M1 1.5 8 7l7-5.5" fill="none" stroke="var(--footer)" stroke-width="1.5"/></svg></span>
    <span>hello@corvellains.com</span>
  </div>
  <div class="abs info-row" style="top:2075px">
    <span class="ring"><svg width="15" height="15" viewBox="0 0 24 24"><path fill="#fff" d="M6.6 10.8a15.1 15.1 0 0 0 6.6 6.6l2.2-2.2c.3-.3.7-.4 1-.2 1.1.4 2.3.6 3.6.6.6 0 1 .4 1 1V20c0 .6-.4 1-1 1A17 17 0 0 1 3 4c0-.6.4-1 1-1h3.5c.6 0 1 .4 1 1 0 1.3.2 2.5.6 3.6.1.3 0 .7-.2 1z"/></svg></span>
    <span>(305) 555-0147</span>
  </div>
  <div class="abs f-label" style="left:810px;top:2136px">SOCIAL</div>
  <div class="abs socials"><span></span><span></span><span></span><span></span><span></span></div>

  <div class="abs f-rule"></div>
  <div class="abs copyright">Copyright &copy; 2016, Corvella Insurance Group. All Rights Reserved.</div>
</footer>

</body>
</html>
```